New business card/stationary for a consulting company

I am looking for a clean and very professional looking business card for my consulting company as well as corresponding stationary. I am uploading our logo. I like simple and powerful for the feel. No graphics but I am open on everything else. Below is my contact information but would like the final to be in a version I can add my employees information into and print. Thank you.

Daniel Whitcombe
dan@ferncliffadvisory.com
2870 North 9th Avenue, Summit Floor, Elm Ridge, Illinois 60531
www.ferncliffadvisory.com

Industry/Entity Type

Consulting

Contact Information for Business Card

Daniel Whitcombe
dan@ferncliffadvisory.com
www.ferncliffadvisory.com

Font styles to use
Serif
Sans Serif

Requirements
Must have
• Our logo and the business card details.
Nice to have
• our website www.ferncliffadvisory.com

```html
<!DOCTYPE html>
<html lang="en">
<head>
<meta charset="utf-8">
<title>Ferncliff Advisory — Business Card</title>
<link href="https://fonts.googleapis.com/css2?family=Roboto:wght@300;400;500&display=swap" rel="stylesheet">
<style>
  :root {
    --backdrop: #5e5f61;
    --card: #232427;
    --card-edge: #1b1c1e;
    --front-ink: #5a5c61;
    --brand-blue: #1d5a92;
    --ink-blue: #1f5186;
    --ink-white: #f2f3f5;
    --rule: #8a8c90;
  }
  * { margin: 0; padding: 0; box-sizing: border-box; }
  html, body { width: 799px; height: 1200px; overflow: hidden; }
  body {
    background: var(--backdrop);
    font-family: "Roboto", Arial, sans-serif;
    position: relative;
  }
  .card {
    position: absolute;
    left: 90px;
    width: 620px;
    height: 354px;
    background: var(--card);
    border: 1px solid var(--card-edge);
    box-shadow: 0 10px 26px rgba(0,0,0,.45);
  }
  .card--front { top: 150px; }
  .card--back { top: 700px; }

  /* front */
  .front-name {
    position: absolute;
    left: 0; right: 0; top: 0; bottom: 0;
    display: flex; align-items: center; justify-content: center; gap: 16px;
  }
  .front-name__square { width: 22px; height: 22px; background: var(--front-ink); flex: none; }
  .front-name__text {
    color: var(--front-ink);
    font-size: 30px; font-weight: 400; letter-spacing: 4px;
    white-space: nowrap;
  }

  /* back */
  .brand-square {
    position: absolute;
    left: 270px; top: 34px;
    width: 80px; height: 64px;
    background: var(--brand-blue);
  }
  .company-name {
    position: absolute; left: 0; right: 0; top: 112px;
    text-align: center;
    color: var(--ink-blue);
    font-size: 34px; font-weight: 400; letter-spacing: 4px;
    white-space: nowrap;
  }
  .rule {
    position: absolute; left: 40px; right: 40px; height: 1px;
    background: linear-gradient(90deg, transparent, var(--rule) 20%, var(--rule) 80%, transparent);
  }
  .rule--top { top: 170px; }
  .rule--bottom { top: 318px; }
  .person-name {
    position: absolute; left: 0; right: 0; top: 186px;
    text-align: center;
    color: var(--ink-blue);
    font-size: 21px; letter-spacing: 2px;
  }
  .contacts {
    position: absolute; left: 50px; top: 234px;
    color: var(--ink-white);
    font-size: 15px; font-weight: 400;
    list-style: none;
  }
  .contacts li { display: flex; align-items: center; gap: 8px; margin-bottom: 12px; white-space: nowrap; }
  .contacts .sep { display: inline-flex; align-items: center; gap: 8px; margin-left: 18px; }
  .contacts svg { width: 13px; height: 13px; fill: var(--ink-white); flex: none; }
</style>
</head>
<body>
  <section class="card card--front">
    <div class="front-name">
      <span class="front-name__square"></span>
      <span class="front-name__text">FERNCLIFF ADVISORY</span>
    </div>
  </section>

  <section class="card card--back">
    <div class="brand-square"></div>
    <h1 class="company-name">FERNCLIFF ADVISORY</h1>
    <div class="rule rule--top"></div>
    <p class="person-name">DANIEL WHITCOMBE</p>
    <ul class="contacts">
      <li>
        <svg viewBox="0 0 16 16" aria-hidden="true"><path d="M1 3h14v10H1z M1 3l7 6 7-6" fill="none" stroke="#f2f3f5" stroke-width="1.6"/></svg>
        <span>dan@ferncliffadvisory.com</span>
        <span class="sep">
          <svg viewBox="0 0 16 16" aria-hidden="true"><circle cx="8" cy="8" r="6.5" fill="none" stroke="#f2f3f5" stroke-width="1.4"/><path d="M1.5 8h13M8 1.5c-3 3.5-3 9.5 0 13M8 1.5c3 3.5 3 9.5 0 13" fill="none" stroke="#f2f3f5" stroke-width="1.2"/></svg>
          <span>www.ferncliffadvisory.com</span>
        </span>
      </li>
      <li>
        <svg viewBox="0 0 16 16" aria-hidden="true"><path d="M8 1a5 5 0 0 0-5 5c0 4 5 9 5 9s5-5 5-9a5 5 0 0 0-5-5zm0 7a2 2 0 1 1 0-4 2 2 0 0 1 0 4z"/></svg>
        <span>2870 North 9th Avenue, Summit Floor, Elm Ridge, Illinois 60531</span>
      </li>
    </ul>
    <div class="rule rule--bottom"></div>
  </section>
</body>
</html>
```